New Business Card for Web Design/Internet Marketing Company

Looking for a great looking new business card. We are a 10 year old web design, internet marketing and website management company that works mostly with small businesses.

Our new card needs to better match the colors and style of our website, be bold, extremely usable and slightly edgy.

Target Market(s)

Small/Medium businesses that have websites

Industry/Entity Type

Internet

Requirements
Must have
• Front and back design, full color, rounded corners please

Must use the colors/style of our website (JPG provided)

INFO FOR CARDS (as readable as possible please)
Mark Lenner
President/CEO
mark@trelvanmedia.example
Phone: 520-381-7459
Toll Free: 866-381-7459
Address: 4315 W. Calloway Ave. Ste. 140, Tucson, AZ 85792

THINGS I WANT TO PROMOTE (if there is room):
1. Our Website - www.trelvanmedia.example

2. Social Media
Twitter: @trelvanmedia
Facebook: www.facebook.com/trelvanmedia

3. Our Services
Web Design
Internet Marketing
Website Management

```html
<!DOCTYPE html>
<html lang="en">
<head>
<meta charset="utf-8">
<title>Trelvan Media – Business Card</title>
<link rel="stylesheet" href="https://fonts.googleapis.com/css2?family=PT+Sans:wght@400;700&display=swap">
<style>
  :root {
    --blue: #1a93cb;
    --blue-deep: #127fb3;
    --orange: #f0862b;
    --ink: #3d3d3d;
    --muted: #6b6b6b;
    --paper: #ffffff;
    --stage: #e7e3de;
  }
  * { margin: 0; padding: 0; box-sizing: border-box; }
  html, body { width: 1200px; height: 758px; overflow: hidden; }
  body {
    background: var(--stage);
    font-family: "PT Sans", sans-serif;
    position: relative;
  }
  .card {
    position: absolute;
    width: 540px;
    height: 310px;
    border-radius: 22px;
    overflow: hidden;
    box-shadow: 0 6px 18px rgba(0,0,0,.18);
  }
  /* Front */
  .card-front { left: 40px; top: 224px; background: var(--paper); }
  .brand {
    position: absolute; left: 30px; top: 112px;
    display: flex; flex-direction: column; align-items: flex-start; gap: 6px;
  }
  .brand-row { display: flex; align-items: center; gap: 9px; white-space: nowrap; }
  .brand-dot { width: 28px; height: 28px; border-radius: 50%; background: var(--orange); flex: none; }
  .brand-name { font-size: 29px; font-weight: 700; color: var(--blue); line-height: 1; white-space: nowrap; }
  .tagline { font-size: 13px; color: var(--ink); padding-left: 37px; white-space: nowrap; }
  .divider {
    position: absolute; left: 268px; top: 40px; width: 2px; height: 168px;
    background: linear-gradient(to bottom, #d0d0d0, #8a8a8a, #d0d0d0);
  }
  .contact { position: absolute; left: 288px; top: 36px; color: var(--ink); }
  .contact-name { font-size: 20px; font-weight: 700; color: var(--orange); line-height: 1.1; }
  .contact-title { font-size: 15px; margin-bottom: 14px; }
  .contact-line { display: flex; align-items: center; gap: 7px; font-size: 13px; line-height: 19px; }
  .contact-line svg { width: 11px; height: 11px; flex: none; }
  .address { font-size: 13px; line-height: 18px; margin-top: 12px; }
  .front-waves { position: absolute; left: 0; bottom: 0; width: 540px; height: 130px; }
  .site-url {
    position: absolute; right: 26px; bottom: 38px;
    font-size: 13px; color: var(--paper);
  }
  /* Back */
  .card-back { left: 620px; top: 224px; background: var(--blue); color: var(--paper); text-align: center; }
  .back-brand {
    position: absolute; left: 0; right: 0; top: 62px;
    display: flex; justify-content: center; align-items: center; gap: 14px;
  }
  .back-brand .brand-dot { width: 48px; height: 48px; background: var(--paper); }
  .back-brand .brand-name { font-size: 50px; color: var(--paper); }
  .services { position: absolute; left: 0; right: 0; top: 160px; }
  .services-title { font-size: 24px; font-weight: 700; margin-bottom: 4px; }
  .services-list { font-size: 19px; line-height: 24px; list-style: none; }
  .socials {
    position: absolute; left: 0; right: 0; bottom: 30px;
    display: flex; justify-content: center; gap: 36px; font-size: 13px;
  }
  .social { display: flex; align-items: center; gap: 6px; }
  .social-box { width: 12px; height: 12px; background: var(--paper); border-radius: 2px; opacity: .85; }
</style>
</head>
<body>
  <section class="card card-front" aria-label="Card front">
    <div class="brand">
      <div class="brand-row">
        <span class="brand-dot"></span>
        <span class="brand-name">Trelvan Media</span>
      </div>
      <span class="tagline">Sites that work harder</span>
    </div>
    <div class="divider"></div>
    <div class="contact">
      <div class="contact-name">Mark Lenner</div>
      <div class="contact-title">President/CEO</div>
      <div class="contact-line">
        <svg viewBox="0 0 12 12"><path d="M3 1l2 2.5-1 1.2c.7 1.4 1.8 2.5 3.2 3.2l1.2-1L11 9l-1.2 1.8C6 10.5 1.5 6 1.2 2.2z" fill="none" stroke="#3d3d3d" stroke-width="1"/></svg>
        866-381-7459
      </div>
      <div class="contact-line">
        <svg viewBox="0 0 12 12"><path d="M3 1l2 2.5-1 1.2c.7 1.4 1.8 2.5 3.2 3.2l1.2-1L11 9l-1.2 1.8C6 10.5 1.5 6 1.2 2.2z" fill="none" stroke="#3d3d3d" stroke-width="1"/></svg>
        520-381-7459
      </div>
      <div class="contact-line">
        <svg viewBox="0 0 12 12"><rect x="1" y="3" width="10" height="7" fill="#3d3d3d"/><path d="M1 3l5 4 5-4" fill="none" stroke="#fff" stroke-width="1"/></svg>
        mark@trelvanmedia.example
      </div>
      <div class="address">4315 W. Calloway Ave. Ste. 140<br>Tucson, AZ 85792</div>
    </div>
    <svg class="front-waves" viewBox="0 0 540 130" preserveAspectRatio="none" aria-hidden="true">
      <path d="M0 88 C130 40 300 30 540 18 L540 130 L0 130Z" fill="var(--blue)"/>
      <path d="M0 104 C140 60 310 50 540 32 L540 130 L0 130Z" fill="var(--paper)"/>
      <path d="M0 112 C150 70 320 56 540 40 L540 130 L0 130Z" fill="var(--orange)"/>
    </svg>
    <div class="site-url">www.trelvanmedia.example</div>
  </section>

  <section class="card card-back" aria-label="Card back">
    <div class="back-brand">
      <span class="brand-dot"></span>
      <span class="brand-name">Trelvan Media</span>
    </div>
    <div class="services">
      <div class="services-title">Our Services</div>
      <ul class="services-list">
        <li>• Web Design • Internet Marketing</li>
        <li>• Website Management</li>
      </ul>
    </div>
    <div class="socials">
      <span class="social"><span class="social-box"></span>@trelvanmedia</span>
      <span class="social"><span class="social-box"></span>trelvanmedia</span>
    </div>
  </section>
</body>
</html>
```